Prayer Service 12.28.2013

I need a flyer designed for a Christian prayer service. The title and theme is:
"Total and Complete Surrender for Total and Complete Deliverance!"
1. You have creative freedom with imagery and typography
2. I need a quick turnaround time
FLYER DETAILS:
A prayer, anointing, and deliverance all night prayer service, at Valleybrook Assembly.
Saturday December 28 2013 from 9pm-6am.
Special guest speakers, prayer,anointing,and deliverance sessions.
For more information contact Sis Rosalind Okafor at Valleybrook Assembly 347 562 9140 Ext. 4816 or Marlene Cobb at 631 208-4392

```html
<!DOCTYPE html>
<html lang="en">
<head>
<meta charset="utf-8">
<title>Total and Complete Surrender — All Night Prayer Service</title>
<link rel="stylesheet" href="https://fonts.googleapis.com/css2?family=Anton&family=Arimo:ital,wght@0,400;0,700;1,400&display=swap">
<style>
  :root {
    --bg: #000000;
    --ink: #ffffff;
    --ink-soft: #d6d6d6;
    --ink-muted: #bdbdbd;
    --glow-core: #fff6ee;
    --glow-red: #6a1d14;
    --photo-dark: #2a1a12;
    --photo-warm: #8a5a3c;
    --photo-light: #d9b79a;
  }
  * { margin: 0; padding: 0; box-sizing: border-box; }
  html, body { width: 834px; height: 1200px; overflow: hidden; background: var(--bg); }
  .flyer {
    position: relative;
    width: 834px;
    height: 1200px;
    background: var(--bg);
    color: var(--ink);
    font-family: "Arimo", Arial, sans-serif;
    overflow: hidden;
  }
  .title {
    position: absolute;
    left: 56px;
    top: 82px;
    font-family: "Anton", "Impact", sans-serif;
    font-weight: 400;
    font-size: 68px;
    line-height: 82px;
    letter-spacing: 1px;
    color: var(--ink);
  }
  .cross-art {
    position: absolute;
    left: 236px;
    top: 318px;
    width: 540px;
    height: 362px;
    background: radial-gradient(ellipse 42% 48% at 53% 48%, var(--glow-core) 0%, #b88b7c 6%, var(--glow-red) 22%, #2b0c08 50%, transparent 72%);
  }
  .intro {
    position: absolute;
    left: 65px;
    top: 373px;
    font-weight: 700;
    font-size: 23px;
    line-height: 30px;
    color: var(--ink);
  }
  .photo {
    position: absolute;
    left: 496px;
    top: 601px;
    width: 306px;
    height: 468px;
    background: linear-gradient(160deg, var(--photo-dark) 0%, var(--photo-warm) 35%, var(--photo-light) 60%, var(--photo-warm) 85%, var(--photo-dark) 100%);
    border-radius: 40% 40% 8px 8px / 22% 22% 8px 8px;
  }
  .schedule {
    position: absolute;
    left: 34px;
    top: 752px;
    width: 410px;
    text-align: center;
  }
  .schedule .day { font-weight: 700; font-size: 38px; line-height: 42px; color: var(--ink-muted); }
  .schedule .date { font-weight: 700; font-size: 18px; line-height: 22px; color: var(--ink-muted); }
  .schedule .time { font-weight: 700; font-size: 27px; line-height: 36px; color: var(--ink-soft); }
  .schedule .program {
    font-style: italic;
    font-weight: 400;
    font-size: 30px;
    line-height: 43px;
    color: var(--ink-muted);
    margin-top: 2px;
  }
  .contact {
    position: absolute;
    left: 46px;
    top: 1118px;
    font-size: 19.5px;
    line-height: 29px;
    color: var(--ink);
  }
</style>
</head>
<body>
  <main class="flyer">
    <h1 class="title">" Total and Complete<br>Surrender for Total and<br>Complete Deliverance! "</h1>

    <div class="cross-art" role="img" aria-label="Glowing white cross with red halo and swirling orbit rings"></div>

    <p class="intro">A prayer, anointing,<br>and deliverance all<br>night prayer service,<br>at Valleybrook<br>Assembly.</p>

    <div class="photo" role="img" aria-label="Photo of a young girl with long hair praying with folded hands"></div>

    <section class="schedule">
      <p class="day">Saturday</p>
      <p class="date">December 28 2013</p>
      <p class="time">from 9pm-6am.</p>
      <p class="program">Special guest speakers,<br>prayer, anointing, and<br>deliverance sessions.</p>
    </section>

    <p class="contact">For more information contact Sis Rosalind Okafor at Valleybrook<br>Assembly 347 562 9140 Ext. 4816 or Marlene Cobb at 631 208-4392</p>
  </main>
</body>
</html>
```